Brimora - Nutritious Snacks and Desserts

We need a creative e-commerce website in which all features--buttons, background, etc.--convey our message: We sell delicious, nutritious snacks and desserts that most closely comply with the paleo diet guidelines. Our first product is Nuttaree®--raw, vegan, paleo chocolate balls that are made of dates, coconut, and cocoa. Our products are organic, raw, irresistible and nutritious. We have several versions of Nuttaree® in development, as well as mousse, ice cream, and crackers. Our mission is to purvey basic healthy foods. Our motto is, "Fuel for the Bold Trail-Walker(tm)."

Target Market(s)

Health-conscious professionals who tend to shop at health food stores. Our products also meet the requirements of a gluten-free diet; and they also don't contain refined sugar, so shoppers with gluten and possibly sugar issues are incidental customers.

Industry/Entity Type

Health Product

Coding

Number of Pages Required

5+ page

Colors

Designer to choose colors to be used in the design.

Requirements
Must have
• We need at least a home page, a products page, an about-us page, a contact page, and a shopping cart page. We would like to be able to add products on our own later. We should be able to handle some basic coding, especially if it's just a matter of copying and modifying product pages. We would also like the ability in the future to add blogging pages, allowing us to write articles about health food and healthy lifestyle, thus attracting web-traffic (SEO).
• Other features we would like to have:
• Product photo slider on the hopepage
• Back-to-top button at the bottom of the home page
• Make sure the site is mobile-compatible
• A search bar at the top of the homepage
• "Create an account" and "Previous orders"--allowing customers to see their previous orders and reorder what they purchased in the past.
Nice to have
• We would like to convey the paleo theme without actually stating it anywhere. We'll add text as necessary, according to the page layout; you can use ipsum lorem for purpose of demonstration.

```html
<!DOCTYPE html>
<html lang="en">
<head>
<meta charset="utf-8">
<title>Brimora – Nutritious snacks and desserts</title>
<link href="https://fonts.googleapis.com/css2?family=Open+Sans:wght@400;600;700&family=Roboto+Condensed:wght@400;700&display=swap" rel="stylesheet">
<style>
:root{
  --green:#5a9a1e;
  --green-dark:#3f6f12;
  --green-band:#4c7d1a;
  --ink:#2b2b2b;
  --muted:#666;
  --light:#f1f1f1;
  --footer:#1e1e1e;
  --footer-bar:#141414;
  --white:#fff;
}
*{box-sizing:border-box;margin:0;padding:0}
html,body{width:1200px;height:3008px;overflow:hidden}
body{font-family:"Open Sans",Arial,sans-serif;color:var(--ink);background:var(--white);position:relative}
.heading{font-family:"Roboto Condensed","Arial Narrow",sans-serif;font-weight:700;text-transform:uppercase;text-align:center;font-size:34px;letter-spacing:1px}

/* header */
.site-header{position:absolute;top:0;left:0;width:1200px;height:144px;background:var(--white)}
.brand{position:absolute;left:40px;top:26px;display:flex;align-items:center;gap:14px}
.brand-dot{width:70px;height:70px;border-radius:50%;background:var(--green)}
.brand-name{font-size:46px;font-weight:700;color:var(--green);letter-spacing:1px}
.top-contact{position:absolute;right:40px;top:18px;display:flex;align-items:center;gap:10px;font-size:17px;color:var(--muted)}
.top-contact .sq{width:20px;height:20px;background:var(--green);border-radius:3px}
.main-nav{position:absolute;right:40px;top:66px;display:flex;gap:10px}
.main-nav a{font-size:18px;color:var(--ink);text-decoration:none;padding:8px 20px;border-radius:20px}
.main-nav a.active{background:var(--green);color:var(--white)}

/* hero */
.hero{position:absolute;top:144px;left:0;width:1200px;height:640px}
.hero-photo{position:absolute;inset:0;background:radial-gradient(ellipse at 50% 45%,#4a4a48 0%,#2e2d2b 55%,#1e1c1a 100%)}
.hero-photo::before{content:"";position:absolute;inset:0;background:linear-gradient(90deg,rgba(170,110,60,.45) 0%,rgba(0,0,0,0) 30%,rgba(0,0,0,0) 70%,rgba(180,40,30,.45) 100%)}
.hero-title{position:absolute;top:300px;width:100%;text-align:center;color:var(--white);font-size:72px;font-weight:600;letter-spacing:4px}
.hero-sub{position:absolute;top:396px;width:100%;text-align:center;color:var(--white);font-size:30px}
.hero-curve{position:absolute;bottom:-2px;left:0}

/* welcome */
.welcome{position:absolute;top:784px;left:0;width:1200px;height:416px}
.video{position:absolute;left:220px;top:52px;width:312px;height:268px;background:linear-gradient(135deg,#cfc8bc,#8b7b66);border:6px solid #ddd}
.play{position:absolute;left:50%;top:50%;width:64px;height:64px;margin:-32px 0 0 -32px;border-radius:50%;background:rgba(0,0,0,.6)}
.play::after{content:"";position:absolute;left:25px;top:18px;border-left:22px solid var(--white);border-top:14px solid transparent;border-bottom:14px solid transparent}
.welcome-copy{position:absolute;left:560px;top:78px;width:560px}
.welcome-copy h2{font-family:"Roboto Condensed",sans-serif;font-size:32px;font-weight:700;text-transform:uppercase;margin-bottom:14px}
.welcome-copy p{font-size:17px;line-height:1.55;color:var(--muted);margin-bottom:16px}

/* features */
.features{position:absolute;top:1200px;left:0;width:1200px;height:480px;background:linear-gradient(180deg,var(--green-band),var(--green-dark));color:var(--white)}
.features .heading{margin-top:62px}
.feature-list{position:absolute;top:160px;left:120px;width:960px;display:flex;justify-content:space-between}
.feature{width:210px;text-align:center}
.feature-icon{width:100px;height:100px;border-radius:50%;background:var(--white);margin:0 auto 14px;display:flex;align-items:center;justify-content:center}
.feature h3{font-size:24px;font-weight:600;margin-bottom:10px}
.feature p{font-size:15px;line-height:1.45;opacity:.9}
.feature a{display:inline-block;margin-top:6px;font-size:15px;color:var(--white);text-decoration:none}
.arrow{position:absolute;top:216px}

/* products */
.products{position:absolute;top:1680px;left:0;width:1200px;height:580px}
.products .heading{margin-top:104px}
.product{position:absolute;top:180px;width:300px;height:300px;background:var(--white);box-shadow:0 2px 10px rgba(0,0,0,.2);padding:10px}
.product-photo{width:280px;height:210px}
.product h3{text-align:center;font-size:22px;font-weight:400;margin-top:22px}

/* news */
.news{position:absolute;top:2260px;left:0;width:1200px;height:420px;background:var(--light)}
.news .heading{margin-top:56px}
.news-item{position:absolute;top:146px;width:500px;height:196px;background:var(--white);display:flex;gap:18px;padding:12px}
.news-photo{width:180px;height:172px;flex:none}
.news-item h4{font-size:17px;font-weight:600;margin-top:6px}
.news-item time{display:block;font-size:13px;color:var(--muted);margin:4px 0 8px}
.news-item p{font-size:14px;line-height:1.45;color:var(--muted)}
.news-item a{display:block;margin-top:8px;font-size:14px;color:var(--green);text-decoration:none}

/* footer */
.site-footer{position:absolute;top:2680px;left:0;width:1200px;height:328px;background:var(--footer);color:#ccc}
.footer-brand{position:absolute;left:88px;top:46px;display:flex;align-items:center;gap:12px}
.footer-brand .brand-dot{width:60px;height:60px}
.footer-brand .brand-name{font-size:38px}
.footer-col{position:absolute;top:44px}
.footer-col h5{font-size:15px;font-weight:600;color:var(--white);text-transform:uppercase;margin-bottom:14px}
.footer-col li{list-style:none;font-size:13px;line-height:1.5;margin-bottom:8px;display:flex;gap:10px}
.footer-col li svg{flex:none;margin-top:2px}
.footer-col p{font-size:13px;line-height:1.5;margin-bottom:12px}
.signup{display:flex}
.signup span{width:150px;height:32px;background:var(--white);color:#999;font-size:13px;padding:7px 10px}
.signup b{height:32px;background:var(--green);color:var(--white);font-size:13px;padding:7px 14px;font-weight:600}
.socials{display:flex;gap:12px}
.socials span{width:32px;height:32px;background:#ccc;border-radius:4px}
.copyright{position:absolute;bottom:0;left:0;width:100%;height:48px;background:var(--footer-bar);text-align:center;font-size:13px;line-height:48px;color:#999}
</style>
</head>
<body>

<header class="site-header">
  <div class="brand"><span class="brand-dot"></span><span class="brand-name">Brimora</span></div>
  <div class="top-contact">
    <svg width="18" height="18" viewBox="0 0 24 24"><path fill="#666" d="M6.6 10.8a15 15 0 0 0 6.6 6.6l2.2-2.2a1 1 0 0 1 1-.25 11.4 11.4 0 0 0 3.6.6 1 1 0 0 1 1 1V20a1 1 0 0 1-1 1A17 17 0 0 1 3 4a1 1 0 0 1 1-1h3.5a1 1 0 0 1 1 1c0 1.25.2 2.45.6 3.6a1 1 0 0 1-.25 1z"/></svg>
    <span>(555) 014-2231</span>
    <span class="sq"></span><span class="sq"></span><span class="sq"></span><span class="sq"></span>
  </div>
  <nav class="main-nav">
    <a class="active" href="#">Home</a><a href="#">Products</a><a href="#">About us</a><a href="#">Services</a><a href="#">Blog</a><a href="#">Contact Us</a>
  </nav>
</header>

<section class="hero">
  <div class="hero-photo" role="img" aria-label="Overhead photo of fresh vegetables, nuts and grains on a dark slate surface"></div>
  <h1 class="hero-title">BRIMORA</h1>
  <p class="hero-sub">Nutritious snacks and desserts</p>
  <svg class="hero-curve" width="1200" height="80" viewBox="0 0 1200 80">
    <path d="M0 20 Q600 100 1200 20 L1200 80 L0 80Z" fill="#fff"/>
    <path d="M0 20 Q600 100 1200 20" fill="none" stroke="#5a9a1e" stroke-width="6"/>
  </svg>
</section>

<section class="welcome">
  <div class="video" role="img" aria-label="Video still of a tub of chocolate treats"><span class="play"></span></div>
  <div class="welcome-copy">
    <h2>Welcome to Brimora Foods</h2>
    <p>Our products are raw, organic, vegan, gluten-free, dairy-free, fiber-rich, nutrient-dense, antioxidant-rich real foods with no preservatives, no added sugar, and no artificial or plant-based sweeteners.</p>
    <p>And they are irresistibly scrumptious!</p>
  </div>
</section>

<section class="features">
  <h2 class="heading">Our Features</h2>
  <svg class="arrow" style="left:60px" width="20" height="36" viewBox="0 0 20 36"><path d="M16 4 L4 18 L16 32" fill="none" stroke="#fff" stroke-width="4"/></svg>
  <svg class="arrow" style="right:60px" width="20" height="36" viewBox="0 0 20 36"><path d="M4 4 L16 18 L4 32" fill="none" stroke="#fff" stroke-width="4"/></svg>
  <div class="feature-list">
    <div class="feature">
      <div class="feature-icon"><svg width="50" height="50" viewBox="0 0 50 50"><path d="M8 42 C8 18 24 8 44 8 C44 30 30 42 8 42Z" fill="#4c7d1a"/></svg></div>
      <h3>Raw</h3><p>It is a long established fact that a reader will be distracted</p><a href="#">Learn More &gt;&gt;</a>
    </div>
    <div class="feature">
      <div class="feature-icon"><svg width="50" height="50" viewBox="0 0 50 50"><path d="M10 40 C10 20 22 10 40 10 C40 30 28 40 10 40Z" fill="#4c7d1a"/><path d="M10 40 L34 16" stroke="#fff" stroke-width="3"/></svg></div>
      <h3>Organic</h3><p>It is a long established fact that a reader will be distracted</p><a href="#">Learn More &gt;&gt;</a>
    </div>
    <div class="feature">
      <div class="feature-icon"><svg width="50" height="50" viewBox="0 0 50 50"><circle cx="25" cy="29" r="15" fill="#4c7d1a"/><path d="M25 14 C25 8 30 6 34 6" fill="none" stroke="#4c7d1a" stroke-width="3"/></svg></div>
      <h3>Vegan</h3><p>It is a long established fact that a reader will be distracted</p><a href="#">Learn More &gt;&gt;</a>
    </div>
    <div class="feature">
      <div class="feature-icon"><svg width="54" height="54" viewBox="0 0 54 54"><circle cx="27" cy="27" r="22" fill="none" stroke="#4c7d1a" stroke-width="4"/><path d="M27 12 V42 M20 20 L27 24 L34 20 M20 30 L27 34 L34 30" fill="none" stroke="#4c7d1a" stroke-width="3"/><path d="M12 12 L42 42" stroke="#4c7d1a" stroke-width="4"/></svg></div>
      <h3>Gluten-free</h3><p>It is a long established fact that a reader will be distracted</p><a href="#">Learn More &gt;&gt;</a>
    </div>
  </div>
</section>

<section class="products">
  <h2 class="heading">Our Products</h2>
  <article class="product" style="left:88px">
    <div class="product-photo" role="img" aria-label="Photo of coconut-coated chocolate balls" style="background:linear-gradient(135deg,#6b5445,#2f241d)"></div>
    <h3>Chocolate Balls</h3>
  </article>
  <article class="product" style="left:450px">
    <div class="product-photo" role="img" aria-label="Photo of colourful ice cream scoops" style="background:linear-gradient(135deg,#f3b8c8,#f2d36b 60%,#9fd0c8)"></div>
    <h3>Ice Cream</h3>
  </article>
  <article class="product" style="left:812px">
    <div class="product-photo" role="img" aria-label="Photo of golden crackers" style="background:linear-gradient(135deg,#e8b46a,#b9792f)"></div>
    <h3>Crackers</h3>
  </article>
</section>

<section class="news">
  <h2 class="heading">Latest News</h2>
  <article class="news-item" style="left:88px">
    <div class="news-photo" role="img" aria-label="Photo of crackers" style="background:linear-gradient(135deg,#e1b36f,#a9702f)"></div>
    <div><h4>Neque porro quisquam</h4><time>09-07-2016</time><p>It is a long established fact that a reader will be distracted by the readable content of a page when looking at its layout.</p><a href="#">Read More &gt;&gt;</a></div>
  </article>
  <article class="news-item" style="left:612px">
    <div class="news-photo" role="img" aria-label="Photo of chocolate balls" style="background:linear-gradient(135deg,#6b5445,#2f241d)"></div>
    <div><h4>Neque porro quisquam</h4><time>09-07-2016</time><p>It is a long established fact that a reader will be distracted by the readable content of a page when looking at its layout.</p><a href="#">Read More &gt;&gt;</a></div>
  </article>
</section>

<footer class="site-footer">
  <div class="footer-brand"><span class="brand-dot"></span><span class="brand-name">Brimora</span></div>
  <div class="footer-col" style="left:364px;width:240px">
    <h5>Contact Us</h5>
    <ul>
      <li><svg width="12" height="14" viewBox="0 0 12 14"><path d="M6 0a5 5 0 0 1 5 5c0 4-5 9-5 9S1 9 1 5a5 5 0 0 1 5-5z" fill="#5a9a1e"/></svg><span>Suite 12, 4480 Larkspur Road, Fernvale, AB</span></li>
      <li><svg width="12" height="12" viewBox="0 0 24 24"><path fill="#5a9a1e" d="M6.6 10.8a15 15 0 0 0 6.6 6.6l2.2-2.2a1 1 0 0 1 1-.25 11.4 11.4 0 0 0 3.6.6 1 1 0 0 1 1 1V20a1 1 0 0 1-1 1A17 17 0 0 1 3 4a1 1 0 0 1 1-1h3.5a1 1 0 0 1 1 1c0 1.25.2 2.45.6 3.6a1 1 0 0 1-.25 1z"/></svg><span>(555) 014-2231</span></li>
      <li><svg width="14" height="12" viewBox="0 0 14 12"><rect x="1" y="1" width="12" height="10" fill="none" stroke="#5a9a1e" stroke-width="1.5"/><path d="M1 1 L7 7 L13 1" fill="none" stroke="#5a9a1e" stroke-width="1.5"/></svg><span>info@brimora.com</span></li>
    </ul>
  </div>
  <div class="footer-col" style="left:650px;width:260px">
    <h5>Join our mailing list</h5>
    <p>Get our news about fresh new treats first.</p>
    <div class="signup"><span>Email address</span><b>Submit</b></div>
  </div>
  <div class="footer-col" style="left:958px;width:180px">
    <h5>Follow us out there</h5>
    <div class="socials"><span></span><span></span><span></span><span></span></div>
  </div>
  <div class="copyright">Copyright © 2016. All Rights Reserved</div>
</footer>

</body>
</html>
```